Corporate Business Card

Very professional, Modern, Not to busy, include phone address email, website
(253) 617-4930, 18761 52nd Avenue S, Kent, WA 98047, martin@plumlinegroup.com, varkoworks.com

Target Market(s)

Manufacturing

Industry/Entity Type

Aero, machining, manufacturing, Off road racing

Contact Information for Business Card

Phone, address email, website

```html
<!DOCTYPE html>
<html lang="en">
<head>
<meta charset="utf-8">
<title>Varko Works – Business Card</title>
<link rel="stylesheet" href="https://fonts.googleapis.com/css2?family=Montserrat:wght@400;500;700;800&display=swap">
<style>
  :root {
    --navy: #17366f;
    --red: #d3202a;
    --white: #ffffff;
    --ink: #222a36;
    --backdrop: #3a3a3c;
  }
  * { box-sizing: border-box; margin: 0; padding: 0; }
  html, body {
    width: 1200px; height: 905px; overflow: hidden;
    background: var(--backdrop);
    font-family: "Montserrat", sans-serif;
  }
  .canvas { position: relative; width: 1200px; height: 905px; }
  .card {
    position: absolute; width: 600px; height: 343px;
    border-radius: 16px; overflow: hidden;
  }
  /* Back of card */
  .card-back { left: 300px; top: 78px; background: var(--navy); }
  .card-back .wordmark {
    position: absolute; left: 0; right: 0; top: 128px;
    text-align: center; color: var(--white);
    font-weight: 800; font-size: 54px; letter-spacing: 1px;
  }
  .card-back .wordmark-rule {
    position: absolute; left: 150px; top: 214px;
    width: 160px; height: 2px; background: var(--white);
  }
  /* Front of card */
  .card-front { left: 300px; top: 484px; background: var(--white); }
  .card-front .wave {
    position: absolute; left: 0; top: 0; width: 600px; height: 343px;
  }
  .card-front .wordmark {
    position: absolute; left: 42px; top: 108px;
    color: var(--navy); font-weight: 800; font-size: 34px; letter-spacing: 0.5px;
  }
  .card-front .wordmark-rule {
    position: absolute; left: 42px; top: 160px;
    width: 110px; height: 2px; background: var(--navy);
  }
  .divider {
    position: absolute; left: 290px; top: 44px;
    width: 1px; height: 166px; background: var(--red);
  }
  .details {
    position: absolute; left: 312px; top: 40px;
    color: var(--ink);
  }
  .person-name {
    font-weight: 800; font-size: 20px; letter-spacing: 0.5px; line-height: 1.1;
  }
  .person-name .first { color: var(--red); }
  .person-name .last { color: var(--navy); }
  .person-role {
    font-size: 11px; font-weight: 500; letter-spacing: 0.5px; margin-top: 2px;
  }
  .address { font-size: 12px; line-height: 1.45; margin-top: 14px; }
  .contacts {
    list-style: none; margin-top: 12px; font-size: 12px; line-height: 1.6;
  }
  .contacts li { display: flex; align-items: center; gap: 7px; }
  .contacts svg { width: 11px; height: 11px; fill: var(--red); flex: none; }
</style>
</head>
<body>
<main class="canvas">

  <section class="card card-back" aria-label="Business card back">
    <div class="wordmark">Varko Works</div>
    <div class="wordmark-rule"></div>
  </section>

  <section class="card card-front" aria-label="Business card front">
    <svg class="wave" viewBox="0 0 600 343" aria-hidden="true">
      <path d="M0,343 C260,343 430,250 610,190 L610,343 Z" fill="var(--navy)"/>
      <path d="M-10,320 C250,318 410,226 610,178" fill="none" stroke="var(--red)" stroke-width="7"/>
    </svg>

    <div class="wordmark">Varko Works</div>
    <div class="wordmark-rule"></div>

    <div class="divider"></div>

    <div class="details">
      <h1 class="person-name"><span class="first">DALEN</span> <span class="last">FORSYTH</span></h1>
      <p class="person-role">FOUNDER</p>
      <p class="address">18761 52nd Avenue S,<br>Kent, WA 98047</p>
      <ul class="contacts">
        <li>
          <svg viewBox="0 0 24 24"><path d="M6.6 10.8a15.1 15.1 0 0 0 6.6 6.6l2.2-2.2a1 1 0 0 1 1-.25 11.4 11.4 0 0 0 3.6.57 1 1 0 0 1 1 1V20a1 1 0 0 1-1 1A17 17 0 0 1 3 4a1 1 0 0 1 1-1h3.5a1 1 0 0 1 1 1c0 1.25.2 2.45.57 3.57a1 1 0 0 1-.25 1z"/></svg>
          (253) 617-4930
        </li>
        <li>
          <svg viewBox="0 0 24 24"><path d="M2 5h20v14H2z M2 5l10 8 10-8" /></svg>
          martin@plumlinegroup.com
        </li>
        <li>
          <svg viewBox="0 0 24 24"><path d="M12 2a10 10 0 1 0 0 20 10 10 0 0 0 0-20zm6.9 6h-2.9a15.7 15.7 0 0 0-1.4-3.6A8 8 0 0 1 18.9 8zM12 4c.8 1.2 1.5 2.5 1.9 4h-3.8c.4-1.5 1.1-2.8 1.9-4zM4.3 14a8 8 0 0 1 0-4h3.4a16 16 0 0 0 0 4zm.8 2h2.9c.3 1.3.8 2.5 1.4 3.6A8 8 0 0 1 5.1 16zM8 8H5.1a8 8 0 0 1 4.3-3.6C8.8 5.5 8.3 6.7 8 8zm4 12c-.8-1.2-1.5-2.5-1.9-4h3.8c-.4 1.5-1.1 2.8-1.9 4zm2.3-6H9.7a14.6 14.6 0 0 1 0-4h4.6a14.6 14.6 0 0 1 0 4zm.3 5.6c.6-1.1 1.1-2.3 1.4-3.6h2.9a8 8 0 0 1-4.3 3.6zm1.7-5.6a16 16 0 0 0 0-4h3.4a8 8 0 0 1 0 4z"/></svg>
          www.varkoworks.com
        </li>
      </ul>
    </div>
  </section>

</main>
</body>
</html>
```